Need App for Impact Related Events

My app is to help with internal events. When you enter the prompted event code the next screen shows you everyone currently at the event. It will give you the ability to Start a conversation with someone you met at that event, or signal it is your turn to send a message. The next screen is a message thread with that person. I am looking for a design that incorporates the colors and ‘feel good’ emotion of our logo. I have pieced together a pretty good interpretation of what I’m looking for in the attached mockup by slicing and dicing designs. I also attached our logo mascot.Screens (see attached mockups)

Note 1: I do not like the picture on the screen used in screen one because it makes it seem like a dating app. I attached an alternative photo that can be used or present different ideas.

Note 2: On the login/signup screen (screen 2) I need an additional first and last name for login, you can try to fit this on one login screen or present a two step signup screen where that is presented in the second screen.

READ MOCKUP GUIDELINES UNDER Must Haves

Target Market(s)

People attending internal social impact events

Industry/Entity Type

Charity

Font styles to use
Sans Serif

Colors
86cfc6

Requirements
Must have
• Follow the screen mockups attached to project
• PLEASE READ
• I have provided a relatively close design of what I’m looking for in the mockups. Some screens need to be followed more closely to my design mockup than other. I have listed a guide below how how closely you should follow my mockup design exactly. Overall I would like to see some ideas of incorporating a few accent colors so it doesn’t appear SO Blue. I also attached some app inspiration designs I found from around the web
• Screen Mockup Guideline Follow %
• Screen 1: 65% - mostly on target, would like to see ways to make it not SO Blue and possibly creative places to add some explainer text describing the app
• Screen 2: 50% - general design idea is here, but more open
• Screen 3: 35% - a lot more room for design influence
• Screen 4: 70% - mostly on target, a little room for design influence/color scheme ideas
• Screen 5-6: 25% - a lot of room for design change/ideas/influence
• Screen 7-8: 80% - already very close to what I need, maybe open to slight sizing and color scheme ideas
• Screen 9: 15% - the most open for influence, only the general functionality of the screen is communicated here
Nice to have
• Please Read Mockup Guideline above. In large part I am looking for something to use some nice accent colors so it is not overwhelmingly blue and bring the whole design into a seamless style.
Should not have

```html
<!DOCTYPE html>
<html lang="en">
<head>
<meta charset="utf-8">
<title>KindHive – App Screens</title>
<link href="https://fonts.googleapis.com/css2?family=Roboto:wght@300;400;500;700&display=swap" rel="stylesheet">
<style>
:root{
  --teal:#00c9c8;
  --teal-dark:#00a9a8;
  --teal-soft:#d9f6f5;
  --ink:#1d1a14;
  --muted:#9aa3a3;
  --line:#cfd8d8;
  --cocoa:#2f2510;
  --white:#ffffff;
  --stage:#f2f4f4;
  --photo-a:#1f5a63;
  --photo-b:#7b6a55;
}
*{box-sizing:border-box;margin:0;padding:0}
html,body{width:1200px;height:1200px;overflow:hidden}
body{background:var(--stage);font-family:'Roboto',Arial,sans-serif;color:var(--ink);position:relative}
.screen{position:absolute;width:198px;height:430px;border-radius:22px;overflow:hidden;background:var(--white);box-shadow:0 6px 20px rgba(0,60,60,.08)}
.screen > *{position:absolute}
.col1{left:100px}.col2{left:374px}.col3{left:647px}.col4{left:921px}
.row1{top:100px}.row2{top:644px}

/* hero photos */
.hero{left:0;top:0;width:198px}
.hero--festival{height:240px;background:linear-gradient(180deg,#2a4f7a 0%,#6a5c6f 45%,#c7c3c8 80%,var(--white) 100%)}
.hero--teal{height:168px;background:linear-gradient(160deg,#12d3d0 0%,#0a8f8c 55%,#0c3b36 100%)}
.hero--mono{height:168px;background:linear-gradient(160deg,#5b5650 0%,#3a3631 55%,#25221f 100%)}
.mascot{border-radius:50%;background:radial-gradient(circle at 40% 40%,#3fe0dc,#0aa7a5 70%,#173b39)}
.mascot--hero{left:62px;top:44px;width:74px;height:74px}
.mascot--corner{left:166px;top:64px;width:30px;height:30px;transform:translateX(-8px)}
.brand{width:198px;left:0;text-align:center;top:124px;font-size:17px;font-weight:500;color:var(--white);letter-spacing:.3px}

/* buttons */
.btn{height:21px;border-radius:11px;display:flex;align-items:center;justify-content:center;font-size:5.5px;font-weight:700;letter-spacing:.4px;text-transform:uppercase}
.btn--primary{background:var(--teal);color:var(--white);box-shadow:0 3px 8px rgba(0,201,200,.35)}
.btn--ghost{background:var(--white);color:var(--teal);box-shadow:0 3px 8px rgba(0,0,0,.07);font-weight:500;text-transform:none;letter-spacing:0}
.btn--light{background:var(--white);color:var(--teal)}
.btn--deep{background:var(--teal);color:var(--white);box-shadow:0 4px 10px rgba(0,80,80,.25)}
.center-75{left:61.5px;width:75px}
.center-111{left:43.5px;width:111px}

/* form */
.label{font-size:4.5px;color:var(--muted);left:18px}
.value{font-size:10px;font-weight:300;color:var(--teal);left:30px}
.rule{height:1px;background:var(--line);left:18px;width:162px}
.remember{left:18px;top:259px;display:flex;align-items:center;gap:9px;font-size:5px;font-weight:500}
.tick{width:8px;height:8px;border-radius:50%;background:var(--teal);display:flex;align-items:center;justify-content:center}
.forgot{right:18px;top:261px;font-size:5px;color:var(--teal);font-weight:500}
.divider{left:12px;width:174px;display:flex;align-items:center;gap:8px;font-size:4.5px;color:var(--muted)}
.divider::before,.divider::after{content:"";flex:1;height:1px;background:var(--line)}
.social{display:flex;align-items:center;gap:3px;font-size:4.5px;color:var(--ink)}
.social-dot{width:13px;height:13px;border-radius:50%;background:var(--teal)}
.footer-note{left:0;width:198px;text-align:center;font-size:5px;color:var(--ink)}
.footer-note span{color:var(--teal)}

/* headings */
.back{left:18px;top:31px;width:18px;height:12px}
.heading{left:18px;top:60px;line-height:1.08}
.heading .light{display:block;font-size:17px;font-weight:300}
.heading .bold{display:block;font-size:17px;font-weight:700}
.gear{right:18px;top:34px;width:11px;height:11px}

/* profile picture */
.tile{top:197px;width:63px;height:63px;border-radius:14px;background:var(--white);box-shadow:0 6px 16px rgba(0,201,200,.18);display:flex;align-items:center;justify-content:center}
.tile-label{top:241px;width:63px;text-align:center;font-size:4.8px;font-weight:500}
.skip{right:22px;top:400px;width:74px;height:19px;border-radius:10px;border:1px solid #c9cfcf;display:flex;align-items:center;justify-content:flex-end;gap:6px;padding-right:4px;font-size:4.8px;font-weight:700}

/* code screens */
.screen--teal{background:var(--teal);color:var(--ink)}
.screen--cocoa{background:var(--cocoa)}
.screen--cocoa .heading{color:var(--teal)}
.field{left:18px;width:162px;top:186px;padding-bottom:4px;font-size:6px;font-style:italic;font-weight:300;border-bottom:1px solid}
.screen--teal .field{color:#d6f7f6;border-color:#7fe4e3}
.screen--cocoa .field{color:#d8d2c4;border-color:#6d6450}

/* list */
.search{left:13px;width:166px;top:123px;border-bottom:1px solid var(--teal-soft);padding-bottom:3px;font-size:4.5px;font-style:italic;color:var(--muted)}
.search svg{position:absolute;right:2px;top:-3px}
.person{left:0;width:198px;height:40px;display:flex;align-items:center;padding:0 16px 0 9px}
.avatar{border-radius:50%;flex:none}
.person .avatar{width:36px;height:36px;margin-right:19px}
.av-1{background:linear-gradient(135deg,#7b8a93,#3b4248)}
.av-2{background:linear-gradient(135deg,#b69a86,#5a4436)}
.av-3{background:linear-gradient(135deg,#d8c0a8,#8a6d58)}
.av-4{background:linear-gradient(135deg,#5a4a45,#221a18)}
.av-5{background:linear-gradient(135deg,#c48c74,#6b3d2e)}
.person-info{flex:1}
.person-name{font-size:6px;font-weight:700}
.person-place{font-size:3.6px;color:var(--muted);margin-top:3px}
.person-aside{font-size:5.2px;color:var(--muted)}
.load-more{left:73px;top:410px;width:52px;height:13px;border-radius:7px;border:1px solid var(--teal-soft);font-size:4.5px;color:var(--teal);display:flex;align-items:center;justify-content:center}

/* chat */
.chat-head{right:18px;top:56px;display:flex;align-items:center;gap:5px}
.chat-head .who{text-align:right}
.chat-head .name{font-size:8px;font-weight:700}
.chat-head .status{font-size:3.8px;color:var(--teal);font-weight:500;margin-top:2px}
.chat-head .avatar{width:36px;height:36px}
.chat-rule{left:0;top:102px;width:198px;height:1px;background:#e3eaea}
.msg-av{width:24px;height:24px}
.bubble{font-size:4.6px;font-weight:700;border-radius:10px;padding:0 12px;display:flex;align-items:center}
.bubble--in{background:var(--teal-soft);color:var(--teal-dark);height:19px}
.bubble--out{background:var(--teal);color:var(--white);height:35px;line-height:1.9;border-radius:16px 16px 4px 16px;flex-direction:column;justify-content:center;align-items:flex-start}
.time{font-size:3.8px;color:var(--muted)}
.seen{display:flex;align-items:center;gap:5px;font-size:3.8px;color:var(--muted)}
.seen .avatar{width:9px;height:9px}
.typing{left:15px;top:357px;display:flex;align-items:center;gap:5px}
.typing .avatar{width:9px;height:9px}
.composer{left:6px;top:393px;width:161px;height:19px;border-radius:10px;border:1px solid #dde6e6;display:flex;align-items:center;padding-left:6px;gap:8px;font-size:4.5px;font-style:italic;color:var(--muted)}
.send{left:149px;top:388px;width:29px;height:29px;border-radius:50%;background:var(--teal);box-shadow:0 0 0 3px var(--teal-soft);display:flex;align-items:center;justify-content:center}
</style>
</head>
<body>

<!-- Welcome -->
<section class="screen col1 row1" aria-label="Welcome">
  <div class="hero hero--festival" role="img" aria-label="Photo of two smiling friends at a colourful outdoor charity run"></div>
  <div class="mascot mascot--hero" role="img" aria-label="Bee mascot"></div>
  <div class="brand">KindHive</div>
  <div class="btn btn--primary center-75" style="top:268px">Login</div>
  <div class="btn btn--ghost center-75" style="top:305px">Register Now</div>
  <div class="divider" style="top:366px">Login with Social</div>
  <div class="social" style="left:64px;top:391px"><span class="social-dot"></span>Linkly</div>
  <div class="social" style="left:116px;top:391px"><span class="social-dot"></span>Chirpa</div>
</section>

<!-- Login (colour) -->
<section class="screen col2 row1" aria-label="Login">
  <div class="hero hero--teal" role="img" aria-label="Teal-toned photo of two friends chatting over coffee"></div>
  <div class="mascot mascot--hero" role="img" aria-label="Bee mascot"></div>
  <div class="brand">KindHive</div>
  <div class="label" style="top:188px">Email Address</div>
  <div class="value" style="top:200px">Milo Tanner</div>
  <div class="rule" style="top:215px"></div>
  <div class="label" style="top:225px">Password</div>
  <div class="rule" style="top:252px"></div>
  <div class="remember"><span class="tick"><svg width="5" height="4" viewBox="0 0 5 4"><path d="M.5 2l1.3 1.3L4.5.6" stroke="#fff" fill="none" stroke-width=".9"/></svg></span>Remember me</div>
  <div class="forgot">Forgot Password?</div>
  <div class="btn btn--primary center-75" style="top:295px">Login</div>
  <div class="divider" style="top:344px">Login with Social</div>
  <div class="social" style="left:64px;top:369px"><span class="social-dot"></span>Linkly</div>
  <div class="social" style="left:116px;top:369px"><span class="social-dot"></span>Chirpa</div>
  <div class="footer-note" style="top:412px">Don't have a account ? <span>Register Now</span></div>
</section>

<!-- Login (mono) -->
<section class="screen col3 row1" aria-label="Login alternative">
  <div class="hero hero--mono" role="img" aria-label="Muted photo of two friends chatting over coffee"></div>
  <div class="mascot mascot--hero" role="img" aria-label="Bee mascot"></div>
  <div class="brand">KindHive</div>
  <div class="label" style="top:188px">Email Address</div>
  <div class="value" style="top:200px">Milo Tanner</div>
  <div class="rule" style="top:215px"></div>
  <div class="label" style="top:225px">Password</div>
  <div class="rule" style="top:252px"></div>
  <div class="remember"><span class="tick"><svg width="5" height="4" viewBox="0 0 5 4"><path d="M.5 2l1.3 1.3L4.5.6" stroke="#fff" fill="none" stroke-width=".9"/></svg></span>Remember me</div>
  <div class="forgot">Forgot Password?</div>
  <div class="btn btn--primary center-75" style="top:295px">Login</div>
  <div class="divider" style="top:344px">Login with Social</div>
  <div class="social" style="left:64px;top:369px"><span class="social-dot"></span>Linkly</div>
  <div class="social" style="left:116px;top:369px"><span class="social-dot"></span>Chirpa</div>
  <div class="footer-note" style="top:412px">Don't have a account ? <span>Register Now</span></div>
</section>

<!-- Add profile picture -->
<section class="screen col4 row1" aria-label="Add profile picture">
  <svg class="back" viewBox="0 0 18 12"><path d="M17 6H2M7 1L2 6l5 5" stroke="#00c9c8" stroke-width="1.6" fill="none"/></svg>
  <h1 class="heading"><span class="light">Add Profile</span><span class="bold">Picture</span></h1>
  <div class="mascot mascot--corner" role="img" aria-label="Bee mascot"></div>
  <div class="tile" style="left:22px"><svg width="12" height="10" viewBox="0 0 12 10"><rect x="1" y="2" width="10" height="7" rx="1.5" stroke="#00c9c8" fill="none"/><circle cx="6" cy="5.5" r="2" stroke="#00c9c8" fill="none"/><path d="M4 2l1-1.2h2L8 2" stroke="#00c9c8" fill="none"/></svg></div>
  <div class="tile" style="left:113px"><svg width="12" height="10" viewBox="0 0 12 10"><rect x="1" y="1" width="10" height="8" rx="1" stroke="#00c9c8" fill="none"/><path d="M2 8l3-3 2 2 1.5-1.5L10 8" stroke="#00c9c8" fill="none"/></svg></div>
  <div class="tile-label" style="left:22px">Take Picture</div>
  <div class="tile-label" style="left:113px">Browse Picture</div>
  <div class="btn btn--primary center-75" style="top:289px">Next</div>
  <div class="skip">SKIP FOR NOW <svg width="12" height="12" viewBox="0 0 12 12"><circle cx="6" cy="6" r="5" stroke="#1d1a14" fill="none" stroke-width="1.2"/><path d="M3.5 6h5M6.5 4l2 2-2 2" stroke="#1d1a14" fill="none" stroke-width="1.1"/></svg></div>
</section>

<!-- Enter kind code -->
<section class="screen screen--teal col1 row2" aria-label="Enter location kind code">
  <svg class="back" viewBox="0 0 18 12"><path d="M17 6H2M7 1L2 6l5 5" stroke="#fff" stroke-width="1.6" fill="none"/></svg>
  <h1 class="heading"><span class="light">Enter Location</span><span class="bold">Kind Code</span></h1>
  <div class="mascot mascot--corner" role="img" aria-label="Bee mascot"></div>
  <div class="field">Type your code here</div>
  <div class="btn btn--light center-111" style="top:221px">Submit</div>
  <div class="btn btn--deep center-111" style="top:349px">Create a kind code</div>
</section>

<!-- Give location name -->
<section class="screen screen--cocoa col2 row2" aria-label="Give your location name">
  <svg class="back" viewBox="0 0 18 12"><path d="M17 6H2M7 1L2 6l5 5" stroke="#fff" stroke-width="1.6" fill="none"/></svg>
  <h1 class="heading"><span class="light">Give Your</span><span class="bold">Location Name</span></h1>
  <div class="mascot mascot--corner" role="img" aria-label="Bee mascot"></div>
  <div class="field">Type your location name (optional)</div>
  <div class="btn btn--primary center-111" style="top:224px">Get your code</div>
</section>

<!-- People met -->
<section class="screen col3 row2" aria-label="Who you've met so far">
  <svg class="back" viewBox="0 0 18 12"><path d="M17 6H2M7 1L2 6l5 5" stroke="#00c9c8" stroke-width="1.6" fill="none"/></svg>
  <svg class="gear" viewBox="0 0 12 12"><path d="M6 0l1 1.6 1.8-.5.3 1.9 1.8.7-.8 1.7L11.5 7l-1.7 1 .2 1.9-1.9-.1L7 11.5 6 10l-1 1.5-1.1-1.7-1.9.1.2-1.9L.5 7l1.4-1.6-.8-1.7 1.8-.7.3-1.9L5 1.6z" fill="#00c9c8"/><circle cx="6" cy="6" r="2" fill="#fff"/></svg>
  <h1 class="heading"><span class="light">Who you've</span><span class="bold">met so far</span></h1>
  <div class="mascot mascot--corner" role="img" aria-label="Bee mascot"></div>
  <div class="search">Search names<svg width="8" height="8" viewBox="0 0 8 8"><circle cx="3.3" cy="3.3" r="2.5" stroke="#00c9c8" fill="none"/><path d="M5.2 5.2L7.5 7.5" stroke="#00c9c8"/></svg></div>
  <div class="person" style="top:150px"><div class="avatar av-1" role="img" aria-label="Portrait photo"></div><div class="person-info"><div class="person-name">Owen Marsh</div><div class="person-place">United States</div></div><svg width="12" height="10" viewBox="0 0 12 10"><path d="M1 1h10v6H5L2.5 9V7H1z" stroke="#00c9c8" fill="none" stroke-width="1.1"/></svg></div>
  <div class="person" style="top:200px"><div class="avatar av-2" role="img" aria-label="Portrait photo"></div><div class="person-info"><div class="person-name">Lena Whitfield</div><div class="person-place">United States</div></div><svg width="12" height="10" viewBox="0 0 12 10"><path d="M2 4V2h7M7 .5L9 2 7 3.5M10 6v2H3M5 9.5L3 8l2-1.5" stroke="#1d1a14" fill="none" stroke-width="1.2"/></svg></div>
  <div class="person" style="top:250px"><div class="avatar av-3" role="img" aria-label="Portrait photo"></div><div class="person-info"><div class="person-name">Nora Castell</div><div class="person-place">United States</div></div><svg width="12" height="10" viewBox="0 0 12 10"><path d="M1 1h10v6H5L2.5 9V7H1z" stroke="#00c9c8" fill="none" stroke-width="1.1"/></svg></div>
  <div class="person" style="top:301px"><div class="avatar av-4" role="img" aria-label="Portrait photo"></div><div class="person-info"><div class="person-name">Ada Pemberton</div><div class="person-place">United States</div></div><div class="person-aside">Great Idea......</div></div>
  <div class="person" style="top:351px"><div class="avatar av-5" role="img" aria-label="Portrait photo"></div><div class="person-info"><div class="person-name">Theo Brandt</div><div class="person-place">United States</div></div><div class="person-aside">Awesome Meeting......</div></div>
  <div class="load-more">Load more...</div>
</section>

<!-- Conversation -->
<section class="screen col4 row2" aria-label="Conversation">
  <svg class="back" viewBox="0 0 18 12"><path d="M17 6H2M7 1L2 6l5 5" stroke="#00c9c8" stroke-width="1.6" fill="none"/></svg>
  <svg class="gear" viewBox="0 0 12 12"><path d="M6 0l1 1.6 1.8-.5.3 1.9 1.8.7-.8 1.7L11.5 7l-1.7 1 .2 1.9-1.9-.1L7 11.5 6 10l-1 1.5-1.1-1.7-1.9.1.2-1.9L.5 7l1.4-1.6-.8-1.7 1.8-.7.3-1.9L5 1.6z" fill="#00c9c8"/><circle cx="6" cy="6" r="2" fill="#fff"/></svg>
  <div class="chat-head"><div class="who"><div class="name">Reed Calloway</div><div class="status">Online</div></div><div class="avatar av-1" role="img" aria-label="Portrait photo"></div></div>
  <div class="chat-rule"></div>
  <div class="avatar av-1 msg-av" style="left:14px;top:128px" role="img" aria-label="Portrait photo"></div>
  <div class="bubble bubble--in" style="left:46px;top:130px">Hey, How was meet up</div>
  <div class="time" style="left:118px;top:155px">9:45 pm</div>
  <div class="bubble bubble--out" style="left:43px;top:190px"><span>Do you want to know more....?</span><span>I met nice girls who willing to help</span></div>
  <div class="avatar av-2 msg-av" style="left:155px;top:197px" role="img" aria-label="Portrait photo"></div>
  <div class="time" style="left:61px;top:231px">9:51 pm</div>
  <div class="avatar av-1 msg-av" style="left:14px;top:264px" role="img" aria-label="Portrait photo"></div>
  <div class="bubble bubble--in" style="left:46px;top:267px">That is awesome. Yes shoot me...</div>
  <div class="seen" style="left:109px;top:289px"><span class="avatar av-2" role="img" aria-label="Portrait photo"></span>Seen</div>
  <div class="typing"><span class="avatar av-2" role="img" aria-label="Portrait photo"></span><svg width="13" height="9" viewBox="0 0 13 9"><rect x=".5" y=".5" width="12" height="6" rx="1.5" stroke="#00c9c8" fill="none"/><path d="M3 6.5L2.5 8.5 5 6.5" stroke="#00c9c8" fill="none"/><circle cx="4" cy="3.5" r=".7" fill="#00c9c8"/><circle cx="6.5" cy="3.5" r=".7" fill="#00c9c8"/><circle cx="9" cy="3.5" r=".7" fill="#00c9c8"/></svg></div>
  <div class="composer"><svg width="8" height="8" viewBox="0 0 8 8"><path d="M6.5 3.5L3.3 6.7a1.6 1.6 0 01-2.3-2.3L4.6.9a1 1 0 011.5 1.5L2.8 5.6" stroke="#9aa3a3" fill="none" stroke-width=".8"/></svg>Type something here...</div>
  <div class="send"><svg width="14" height="14" viewBox="0 0 14 14"><circle cx="7" cy="7" r="6" stroke="#fff" fill="none" stroke-width="1.2"/><path d="M3.8 7.2l6-3-2.3 6-1-2.2z" stroke="#fff" fill="none" stroke-width=".9" stroke-linejoin="round"/></svg></div>
</section>

</body>
</html>
```